Business Card Design

My business is writing crime novels to entertain readers. I write legal thrillers and mysteries. I need a card for publishers, agents, other authors, and media.

Industry/Entity Type

Legal

Contact Information for Business Card

Paul Derrow
www.derrowfiction.example
pauljderrow@inkpost.example
0064 27 5190472

```html
<!DOCTYPE html>
<html lang="en">
<head>
<meta charset="utf-8">
<title>Paul Derrow – Business Card</title>
<link href="https://fonts.googleapis.com/css2?family=Exo+2:wght@400;600;700&display=swap" rel="stylesheet">
<style>
  :root {
    --crimson: #a01f24;
    --crimson-dark: #7d1519;
    --ink: #1b1b1b;
    --steel: #8a8a8a;
    --steel-light: #d4d4d4;
    --text-grey: #555555;
    --paper: #ffffff;
    --backdrop: #e9e7e4;
  }
  * { margin: 0; padding: 0; box-sizing: border-box; }
  html, body {
    width: 1200px;
    height: 873px;
    overflow: hidden;
    background: var(--backdrop);
    font-family: "Exo 2", sans-serif;
  }
  .business-card {
    position: absolute;
    left: 150px;
    top: 179px;
    width: 900px;
    height: 514px;
    background: var(--paper);
    overflow: hidden;
    box-shadow: 0 6px 24px rgba(0,0,0,0.18);
  }
  .card-shapes {
    position: absolute;
    inset: 0;
  }
  .portrait {
    position: absolute;
    left: 44px;
    top: 40px;
    width: 340px;
    height: 236px;
    border-radius: 26px;
    background: linear-gradient(135deg, #9a9a9a 0%, #6f6f6f 55%, #3a3a3a 100%);
  }
  .name-band {
    position: absolute;
    left: 440px;
    top: 176px;
    right: 0;
    height: 64px;
    background: var(--crimson);
    display: flex;
    align-items: center;
    padding-left: 34px;
  }
  .author-name {
    color: var(--paper);
    font-weight: 700;
    font-size: 40px;
    letter-spacing: 1px;
    text-transform: uppercase;
  }
  .author-name .mixed { text-transform: none; }
  .genre-line {
    position: absolute;
    left: 500px;
    top: 256px;
    color: var(--crimson);
    font-weight: 600;
    font-size: 20px;
    line-height: 24px;
    letter-spacing: 1.5px;
    text-transform: uppercase;
  }
  .contact-list {
    position: absolute;
    left: 468px;
    top: 320px;
    display: flex;
    gap: 10px;
  }
  .contact-icons {
    display: flex;
    flex-direction: column;
    gap: 4px;
    padding-top: 2px;
  }
  .contact-icons svg { display: block; }
  .contact-lines {
    list-style: none;
    color: var(--text-grey);
    font-size: 17px;
    line-height: 24px;
  }
  .website {
    position: absolute;
    left: 470px;
    bottom: 12px;
    color: var(--paper);
    font-size: 22px;
    letter-spacing: 1.5px;
    font-weight: 600;
  }
</style>
</head>
<body>
  <article class="business-card">
    <svg class="card-shapes" width="900" height="514" viewBox="0 0 900 514" aria-hidden="true">
      <defs>
        <linearGradient id="steelStripe" x1="0" y1="0" x2="1" y2="0">
          <stop offset="0" stop-color="var(--steel-light)"/>
          <stop offset="1" stop-color="var(--steel)"/>
        </linearGradient>
        <linearGradient id="crimsonBand" x1="0" y1="0" x2="1" y2="0">
          <stop offset="0" stop-color="var(--crimson-dark)"/>
          <stop offset="1" stop-color="var(--crimson)"/>
        </linearGradient>
      </defs>
      <!-- bottom stripe set -->
      <polygon points="0,452 420,452 400,472 0,472" fill="url(#steelStripe)"/>
      <polygon points="0,472 400,472 392,482 0,482" fill="var(--ink)"/>
      <polygon points="0,482 392,482 384,492 0,492" fill="var(--paper)"/>
      <rect x="0" y="492" width="900" height="22" fill="var(--crimson)"/>
      <!-- website band -->
      <polygon points="440,452 900,452 900,514 380,514" fill="url(#crimsonBand)"/>
    </svg>

    <div class="portrait" role="img" aria-label="Portrait photograph of the author in a dark shirt against a grey backdrop"></div>

    <div class="name-band">
      <h1 class="author-name">Paul Derrow</h1>
    </div>

    <p class="genre-line">Legal Thrillers<br>and Mysteries Writing</p>

    <div class="contact-list">
      <div class="contact-icons">
        <svg width="20" height="20" viewBox="0 0 20 20" aria-label="Phone">
          <rect width="20" height="20" rx="3" fill="var(--crimson)"/>
          <rect x="7" y="3.5" width="6" height="13" rx="1.2" fill="none" stroke="#fff" stroke-width="1.5"/>
          <circle cx="10" cy="14" r="0.9" fill="#fff"/>
        </svg>
        <svg width="20" height="20" viewBox="0 0 20 20" aria-label="Email">
          <rect width="20" height="20" rx="3" fill="var(--crimson)"/>
          <rect x="4" y="6" width="12" height="8.5" fill="none" stroke="#fff" stroke-width="1.4"/>
          <polyline points="4,6 10,11 16,6" fill="none" stroke="#fff" stroke-width="1.4"/>
        </svg>
        <svg width="20" height="20" viewBox="0 0 20 20" aria-label="Social page">
          <rect width="20" height="20" rx="3" fill="var(--crimson)"/>
        </svg>
      </div>
      <ul class="contact-lines">
        <li>0064 27 5190472</li>
        <li>pauljderrow@inkpost.example</li>
        <li>fablepage.example/PaulDerrowAuthor</li>
      </ul>
    </div>

    <p class="website">www.derrowfiction.example</p>
  </article>
</body>
</html>
```